UI/ UX Design for ERP Software

We need a new UX/UI interface for a ERP software for property managers. Our CMMS / ERP solution is made based on responsive design technologies and is coded in PHP.
The overall UX to be similar to Tev Ulna - easy navigation, intuitive menus.

Industry/Entity Type

Property Management

Number of Pages Required

5+ page

Requirements
Must have
• Round dock buttons
Consistent icons across the application
Enough Spacing between buttons/icons/ menu
Consistent Font
Nice to have
• We would like the UX to allow the users to use the application without /minimum training.
Should not have
• we don't want anything that is classic with respect to UX

```html
<!DOCTYPE html>
<html lang="en">
<head>
<meta charset="utf-8">
<title>Estavo – Active Dashboard</title>
<link href="https://fonts.googleapis.com/css2?family=Roboto:wght@400;500;700&display=swap" rel="stylesheet">
<style>
:root{
  --blue-top:#0a7ef0;
  --blue-bright:#1aa3ff;
  --tab:#0a80f2;
  --tab-active:#18a0f7;
  --accent:#1a9ff5;
  --ink:#1b1b1b;
  --muted:#555;
  --grid:#e4e4e4;
  --panel:#f4f4f4;
  --c-sched:#7db4ea;
  --c-done-sched:#95e57c;
  --c-future:#fb9f54;
  --c-orders:#434348;
  --c-done-orders:#8582e0;
  --c-insp:#e46586;
  --c-done-insp:#e8d058;
}
*{box-sizing:border-box;margin:0;padding:0}
html,body{width:1200px;height:821px;overflow:hidden;background:#fff;font-family:'Roboto',sans-serif;color:var(--ink)}
.topbar{position:absolute;left:0;top:0;width:1200px;height:56px;background:linear-gradient(90deg,var(--blue-top),var(--blue-bright));box-shadow:0 2px 4px rgba(0,0,0,.15)}
.brand{position:absolute;left:22px;top:14px;display:flex;align-items:center;gap:7px;color:#fff;font-size:22px;font-weight:500}
.brand-dot{width:18px;height:18px;background:#fff;border-radius:3px}
.nav-item{position:absolute;top:18px;display:flex;align-items:center;gap:8px;color:#fff;font-size:13.5px;font-weight:500}
.nav-item svg{width:15px;height:15px;fill:#fff}
.tool{position:absolute;top:19px}
.tool svg{width:16px;height:16px;fill:#fff}
.avatar{position:absolute;left:1088px;top:6px;width:44px;height:44px;border-radius:50%;border:2px solid #cfe6ff;background:radial-gradient(circle at 50% 45%,#d9d2cb,#5b6b82)}
.card{position:absolute;left:58px;top:86px;width:1086px;height:658px;background:#fff;box-shadow:0 1px 6px rgba(0,0,0,.2)}
.stats{position:absolute;left:0;top:0;width:100%;height:56px;background:var(--panel)}
.page-title{position:absolute;left:25px;top:20px;display:flex;align-items:center;gap:12px;font-size:14px;font-weight:500}
.page-title svg,.stat svg{fill:var(--accent)}
.stat{position:absolute;top:14px}
.stat svg{position:absolute;left:0;top:0;width:13px;height:13px}
.stat-label{position:absolute;top:0;font-size:11px;font-weight:700;letter-spacing:.3px;white-space:nowrap}
.stat-value{position:absolute;top:18px;font-size:14px;color:var(--accent);white-space:nowrap}
.divider{position:absolute;top:10px;width:1px;height:38px;background:#dcdcdc}
.tabs{position:absolute;left:0;top:56px;width:100%;height:45px;display:flex;background:var(--tab)}
.tab{height:45px;display:flex;align-items:center;justify-content:center;gap:10px;color:#fff;font-size:14px;font-weight:500;letter-spacing:.3px;border-right:1px solid rgba(255,255,255,.35)}
.tab:last-child{border-right:none}
.tab svg{width:13px;height:13px}
.tab.active{background:var(--tab-active);box-shadow:0 3px 6px rgba(0,0,0,.25);height:46px;position:relative;z-index:1}
.range{position:absolute;left:44px;top:153px;display:flex;align-items:center;gap:14px;font-size:21px;font-weight:500;letter-spacing:.5px}
.chart{position:absolute;left:38px;top:202px;width:784px;height:392px}
.legend{position:absolute;left:823px;top:256px;list-style:none}
.legend li{position:absolute;left:0;display:flex;align-items:center;gap:20px;font-size:12px;font-weight:500;color:var(--muted);white-space:nowrap}
.swatch{width:22px;height:18px;display:block}
.footer{position:absolute;left:0;top:774px;width:1200px;text-align:center;font-size:13px;color:var(--muted)}
</style>
</head>
<body>
<header class="topbar">
  <div class="brand"><span class="brand-dot"></span>Estavo</div>
  <nav>
    <div class="nav-item" style="left:195px"><svg viewBox="0 0 16 16"><path d="M8 1 0 8h2v7h4v-5h4v5h4V8h2z"/></svg>Dashboards</div>
    <div class="nav-item" style="left:314px"><svg viewBox="0 0 16 16"><circle cx="8" cy="5" r="3"/><circle cx="3" cy="6" r="2"/><circle cx="13" cy="6" r="2"/><path d="M2 14c0-3 3-5 6-5s6 2 6 5zM0 13c0-2 1-3 3-3v3zM16 13c0-2-1-3-3-3v3z"/></svg>Customers</div>
    <div class="nav-item" style="left:432px"><svg viewBox="0 0 16 16"><path d="M8 1 0 8h2v7h4v-5h4v5h4V8h2z"/></svg>Properties</div>
    <div class="nav-item" style="left:551px"><svg viewBox="0 0 16 16"><path d="M8 0a8 8 0 1 0 0 16A8 8 0 0 0 8 0zm0 2a6 6 0 0 1 4.6 9.8C11.5 10.7 9.9 10 8 10s-3.5.7-4.6 1.8A6 6 0 0 1 8 2zm0 1.5A2.5 2.5 0 1 0 8 8.5 2.5 2.5 0 0 0 8 3.5z"/></svg>Tenants</div>
    <div class="nav-item" style="left:669px"><svg viewBox="0 0 16 16"><circle cx="8" cy="4.5" r="3.5"/><path d="M2 16c0-4 3-6 6-6s6 2 6 6z"/></svg>Contacts</div>
    <div class="nav-item" style="left:789px"><svg viewBox="0 0 16 16"><path d="M0 2h3v3H0zM5 2h11v3H5zM0 7h3v3H0zM5 7h11v3H5zM0 12h3v3H0zM5 12h11v3H5z"/></svg>More<svg viewBox="0 0 16 16" style="width:10px;margin-left:4px"><path d="M2 5l6 6 6-6" stroke="#fff" stroke-width="2.2" fill="none"/></svg></div>
  </nav>
  <div class="tool" style="left:984px"><svg viewBox="0 0 16 16"><path d="M7 0h2l.4 2.2 1.6.7 1.9-1.3 1.4 1.4-1.3 1.9.7 1.6L16 7v2l-2.2.4-.7 1.6 1.3 1.9-1.4 1.4-1.9-1.3-1.6.7L9 16H7l-.4-2.2-1.6-.7-1.9 1.3-1.4-1.4 1.3-1.9-.7-1.6L0 9V7l2.2-.4.7-1.6-1.3-1.9L3 1.7l1.9 1.3 1.6-.7zM8 5.5a2.5 2.5 0 1 0 0 5 2.5 2.5 0 0 0 0-5z"/></svg></div>
  <div class="tool" style="left:1029px"><svg viewBox="0 0 16 16"><path d="M8 0c.6 0 1 .4 1 1v.6c2.3.5 4 2.5 4 4.9V10l2 2.5V13H1v-.5L3 10V6.5c0-2.4 1.7-4.4 4-4.9V1c0-.6.4-1 1-1zM6 14h4a2 2 0 0 1-4 0z"/></svg></div>
  <div class="avatar" role="img" aria-label="User profile photo"></div>
</header>

<main class="card">
  <section class="stats">
    <div class="page-title"><svg viewBox="0 0 16 16" width="16" height="16"><path d="M8 1 0 8h2v7h4v-5h4v5h4V8h2z"/></svg>Active Dashboard</div>
    <div class="stat" style="left:292px"><svg viewBox="0 0 16 16"><path d="M8 1 0 8h2v7h4v-5h4v5h4V8h2z"/></svg><span class="stat-label" style="left:22px">PROPERTIES</span><span class="stat-value" style="left:14px">3</span></div>
    <div class="divider" style="left:416px"></div>
    <div class="stat" style="left:444px"><svg viewBox="0 0 16 16"><circle cx="8" cy="5" r="3"/><circle cx="3" cy="6" r="2"/><circle cx="13" cy="6" r="2"/><path d="M2 14c0-3 3-5 6-5s6 2 6 5zM0 13c0-2 1-3 3-3v3zM16 13c0-2-1-3-3-3v3z"/></svg><span class="stat-label" style="left:23px">TENANTS</span><span class="stat-value" style="left:23px">8</span></div>
    <div class="divider" style="left:565px"></div>
    <div class="stat" style="left:604px"><svg viewBox="0 0 16 16"><path d="M0 0h6L4 2l3 3-2 2-3-3-2 2zM16 0v6l-2-2-3 3-2-2 3-3-2-2zM0 16v-6l2 2 3-3 2 2-3 3 2 2zM16 16h-6l2-2-3-3 2-2 3 3 2-2z"/></svg><span class="stat-label" style="left:21px">PROPERTIES AREA</span><span class="stat-value" style="left:21px">422,000.00 sqft</span></div>
    <div class="divider" style="left:759px"></div>
    <div class="stat" style="left:784px"><svg viewBox="0 0 16 16"><path d="M0 0h6L4 2l3 3-2 2-3-3-2 2zM16 0v6l-2-2-3 3-2-2 3-3-2-2zM0 16v-6l2 2 3-3 2 2-3 3 2 2zM16 16h-6l2-2-3-3 2-2 3 3 2-2z"/></svg><span class="stat-label" style="left:20px">RENTED AREA</span><span class="stat-value" style="left:20px">422,000.00 sqft</span></div>
    <div class="divider" style="left:921px"></div>
    <div class="stat" style="left:945px"><svg viewBox="0 0 16 16"><path d="M0 0h6L4 2l3 3-2 2-3-3-2 2zM16 0v6l-2-2-3 3-2-2 3-3-2-2zM0 16v-6l2 2 3-3 2 2-3 3 2 2zM16 16h-6l2-2-3-3 2-2 3 3 2-2z"/></svg><span class="stat-label" style="left:22px">VACANCIES</span><span class="stat-value" style="left:22px">422,000.00 sqft</span></div>
  </section>

  <nav class="tabs">
    <div class="tab active" style="width:182px"><svg viewBox="0 0 16 16"><circle cx="8" cy="8" r="6.5" fill="none" stroke="#fff" stroke-width="2"/><path d="M8 4v4.5h3" stroke="#fff" stroke-width="2" fill="none"/></svg>LAST 7 DAYS</div>
    <div class="tab" style="width:179px"><svg viewBox="0 0 16 16"><circle cx="8" cy="8" r="6.5" fill="none" stroke="#fff" stroke-width="2"/><path d="M8 4v4.5h3" stroke="#fff" stroke-width="2" fill="none"/></svg>LAST MONTHS</div>
    <div class="tab" style="width:178px"><svg viewBox="0 0 16 16"><circle cx="8" cy="8" r="6.5" fill="none" stroke="#fff" stroke-width="2"/><path d="M8 4v4.5h3" stroke="#fff" stroke-width="2" fill="none"/></svg>LAST 3 MONTHS</div>
    <div class="tab" style="width:186px"><svg viewBox="0 0 16 16"><circle cx="8" cy="8" r="6.5" fill="none" stroke="#fff" stroke-width="2"/><path d="M8 4v4.5h3" stroke="#fff" stroke-width="2" fill="none"/></svg>LAST 7 DAYS</div>
    <div class="tab" style="width:182px"><svg viewBox="0 0 16 16"><circle cx="8" cy="8" r="6.5" fill="none" stroke="#fff" stroke-width="2"/><path d="M8 4v4.5h3" stroke="#fff" stroke-width="2" fill="none"/></svg>NEXT MONTHS</div>
    <div class="tab" style="width:179px"><svg viewBox="0 0 16 16"><circle cx="8" cy="8" r="6.5" fill="none" stroke="#fff" stroke-width="2"/><path d="M8 4v4.5h3" stroke="#fff" stroke-width="2" fill="none"/></svg>NEXT 3 MONTHS</div>
  </nav>

  <h2 class="range"><svg viewBox="0 0 24 20" width="23" height="19"><path d="M1 0v19h23" stroke="#1a7ff0" stroke-width="2" fill="none"/><path d="M5 9h2.5v8H5zM9.5 5H12v12H9.5zM14 10h2.5v7H14zM18.5 7H21v10h-2.5z" fill="#1a7ff0"/></svg>12/27/2021 - 01/03/2021</h2>

  <svg class="chart" viewBox="120 360 980 490" font-family="Roboto, sans-serif">
    <g stroke="var(--grid)" stroke-width="1">
      <line x1="183" y1="428" x2="1088" y2="428"/>
      <line x1="183" y1="505" x2="1088" y2="505"/>
      <line x1="183" y1="582" x2="1088" y2="582"/>
      <line x1="183" y1="659" x2="1088" y2="659"/>
      <line x1="183" y1="736" x2="1088" y2="736"/>
      <line x1="183" y1="813" x2="1088" y2="813"/>
      <line x1="198" y1="366" x2="198" y2="828"/>
      <line x1="310" y1="813" x2="310" y2="828"/>
      <line x1="422" y1="813" x2="422" y2="828"/>
      <line x1="535" y1="813" x2="535" y2="828"/>
      <line x1="648" y1="813" x2="648" y2="828"/>
      <line x1="761" y1="813" x2="761" y2="828"/>
      <line x1="873" y1="813" x2="873" y2="828"/>
      <line x1="986" y1="813" x2="986" y2="828"/>
      <line x1="1088" y1="813" x2="1088" y2="828"/>
    </g>
    <g font-size="15" fill="#333" font-weight="500">
      <text x="143" y="434">1.25</text>
      <text x="143" y="511">1</text>
      <text x="143" y="588">0.75</text>
      <text x="143" y="665">0.5</text>
      <text x="143" y="742">0.25</text>
      <text x="143" y="819">0</text>
    </g>
    <rect x="310" y="659" width="28" height="154" fill="var(--c-done-sched)"/>
    <rect x="423" y="736" width="28" height="77" fill="var(--c-future)"/>
    <rect x="536" y="505" width="28" height="308" fill="var(--c-sched)"/>
    <rect x="649" y="582" width="28" height="231" fill="var(--c-orders)"/>
    <rect x="761" y="428" width="28" height="385" fill="var(--c-done-orders)"/>
    <rect x="874" y="659" width="28" height="154" fill="var(--c-insp)"/>
    <rect x="987" y="502" width="28" height="311" fill="var(--c-done-insp)"/>
    <g font-size="11" fill="#555" text-anchor="middle">
      <text x="256" y="839">12/27/2020</text>
      <text x="369" y="839">12/28/2020</text>
      <text x="481" y="839">12/29/2020</text>
      <text x="594" y="839">12/30/2020</text>
      <text x="707" y="839">12/31/2020</text>
      <text x="820" y="839">01/01/2020</text>
      <text x="932" y="839">01/02/2020</text>
      <text x="1045" y="839">01/03/2020</text>
    </g>
  </svg>

  <ul class="legend">
    <li style="top:0"><span class="swatch" style="background:var(--c-sched)"></span>Scheduled Maintainance</li>
    <li style="top:49px"><span class="swatch" style="background:var(--c-done-sched)"></span>completed Scheduled Maintainance</li>
    <li style="top:97px"><span class="swatch" style="background:var(--c-future)"></span>Future Scheduled Maintainance</li>
    <li style="top:146px"><span class="swatch" style="background:var(--c-orders)"></span>Scheduled work orders</li>
    <li style="top:194px"><span class="swatch" style="background:var(--c-done-orders)"></span>completed work orders</li>
    <li style="top:243px"><span class="swatch" style="background:var(--c-insp)"></span>property inspections in progress</li>
    <li style="top:291px"><span class="swatch" style="background:var(--c-done-insp)"></span>completed property inspections</li>
  </ul>
</main>

<footer class="footer">© 2021 ERP Software. All Rights Reserved</footer>
</body>
</html>
```